Car transport business

We need a new business card design. Attached is our old card sample. I would just like to adjust the logo colors (blue and red) to be brighter. I changed my name to the brighter red and the word dispatcher to a brighter blue as an example. But you can adjust those colors further. And then perhaps you can use the same colors for the card design but use your imagination.

As a suggestion so the card stands out I would like to add a clip art of car carrier truck. Attached are examples of that as well

```html
<!DOCTYPE html>
<html lang="en">
<head>
<meta charset="utf-8">
<title>Northlane Haul – Business Card</title>
<link href="https://fonts.googleapis.com/css2?family=Montserrat:wght@400;500;600&display=swap" rel="stylesheet">
<style>
  :root {
    --backdrop: #dcdcdc;
    --paper: #ffffff;
    --brand-blue: #175a87;
    --brand-red: #be1e2d;
    --back-mark: #3d97d8;
  }
  * { margin: 0; padding: 0; box-sizing: border-box; }
  html, body {
    width: 1200px; height: 1200px; overflow: hidden;
    background: var(--backdrop);
    font-family: "Montserrat", Arial, sans-serif;
  }
  .card {
    position: absolute; left: 207px;
    width: 786px; height: 449px;
    overflow: hidden;
  }
  .card-front { top: 112px; background: var(--paper); }
  .card-back { top: 640px; background: var(--brand-blue); }

  .brand {
    position: absolute; display: flex; align-items: center;
    font-weight: 600; white-space: nowrap;
  }
  .brand-dot { border-radius: 50%; flex: none; }
  .card-front .brand { left: 58px; top: 212px; gap: 12px; font-size: 27px; color: var(--brand-blue); letter-spacing: 0.5px; }
  .card-front .brand-dot { width: 26px; height: 26px; background: var(--brand-red); }

  .divider {
    position: absolute; left: 407px; top: 153px;
    width: 1.5px; height: 144px; background: var(--brand-red);
  }
  .person {
    position: absolute; left: 441px; top: 152px;
    white-space: nowrap;
  }
  .person-name {
    font-size: 34px; font-weight: 600; color: var(--brand-red);
    line-height: 1; letter-spacing: 0.2px;
  }
  .person-role {
    font-size: 20px; font-weight: 400; color: var(--brand-blue);
    line-height: 1.2; margin-top: 5px; letter-spacing: 0.3px;
  }
  .contacts {
    position: absolute; left: 441px; top: 226px; list-style: none;
    white-space: nowrap;
  }
  .contacts li {
    display: flex; align-items: center; gap: 8px;
    height: 25.5px; font-size: 19px; color: var(--brand-blue);
  }
  .contacts svg { width: 16px; height: 16px; flex: none; fill: var(--brand-red); }

  .stripes { position: absolute; left: 0; top: 410px; width: 786px; height: 19px; }

  .card-back .brand { left: 50%; top: 50%; transform: translate(-50%, -50%); gap: 18px; font-size: 50px; color: var(--back-mark); letter-spacing: 1px; }
  .card-back .brand-dot { width: 46px; height: 46px; background: var(--back-mark); }
</style>
</head>
<body>
  <section class="card card-front">
    <div class="brand"><span class="brand-dot"></span>NORTHLANE HAUL</div>
    <div class="divider"></div>
    <div class="person">
      <div class="person-name">MILO RENSHAW</div>
      <div class="person-role">DISPATCHER</div>
    </div>
    <ul class="contacts">
      <li>
        <svg viewBox="0 0 24 24" aria-hidden="true"><path d="M6.6 2.5l2.6 4.3-1.8 1.9c.9 2.6 3.1 5.2 5.6 6.6l2-1.6 4.3 2.6-1.4 3.8C11.4 20.3 3.6 12.5 2.8 3.9z"/></svg>
        555-318-2047
      </li>
      <li>
        <svg viewBox="0 0 24 24" aria-hidden="true"><path d="M6 2h10l2 2v4H6zM2 9h20v9h-4v-4H6v4H2zM7 15h10v7H7z"/></svg>
        555-318-2090
      </li>
      <li>
        <svg viewBox="0 0 24 24" aria-hidden="true"><path d="M2 5h20v14H2zm2 2v.6l8 5.6 8-5.6V7zm0 3v7h16v-7l-8 5.6z" fill-rule="evenodd"/></svg>
        northlanehaul@example.com
      </li>
    </ul>
    <svg class="stripes" viewBox="0 0 786 19" aria-hidden="true">
      <polygon points="0,0 383,0 402,19 0,19" fill="var(--brand-blue)"/>
      <polygon points="395,0 786,0 786,19 414,19" fill="var(--brand-red)"/>
    </svg>
  </section>

  <section class="card card-back">
    <div class="brand"><span class="brand-dot"></span>NORTHLANE HAUL</div>
  </section>
</body>
</html>
```